Business cards for Harbourline Supply Pty Ltd that import building products into Australia from China
Target Market(s)
Business to Business
Industry/Entity Type
Business
Contact Information for Business Card
Front: Logo and Business Name
Rear:
Desmond Varrick
General Manager
Mobile: 0427 561 394
email: dessie@harbourlinesupply.com.au
alternative email: dessie@outbackworks.com.au
web: www.harbourlinesupply.com.au
Adelaide, Brisbane and Darwin
Colors
ec1f27
fbee3d

```html
<!DOCTYPE html>
<html lang="en">
<head>
<meta charset="utf-8">
<title>Harbourline Supply Pty Ltd – Business Cards</title>
<link rel="stylesheet" href="https://fonts.googleapis.com/css2?family=Montserrat:wght@400;500;700;800&display=swap">
<style>
  :root {
    --brand-red: #ec1f27;
    --brand-yellow: #fbee3d;
    --card-black: #070707;
    --ink-white: #ffffff;
    --stage: #3a3a3a;
    --divider: #cfcfcf;
  }
  * { box-sizing: border-box; margin: 0; padding: 0; }
  html, body {
    width: 1200px; height: 864px; overflow: hidden;
    background: var(--stage);
    font-family: "Montserrat", Arial, sans-serif;
  }
  .canvas {
    width: 1200px; height: 864px;
    display: flex; flex-direction: column;
    align-items: center; justify-content: center; gap: 40px;
  }
  .card {
    width: 620px; height: 354px;
    border-radius: 22px;
    position: relative;
    box-shadow: 0 14px 30px rgba(0,0,0,0.45);
  }
  /* Front */
  .card-front {
    background: var(--brand-red);
    display: flex; flex-direction: column; align-items: center; justify-content: center;
  }
  .brand {
    display: flex; align-items: center; gap: 16px;
    margin-top: 10px;
  }
  .brand-dot {
    width: 22px; height: 22px; border-radius: 50%;
    background: var(--brand-yellow);
  }
  .brand-name {
    color: var(--ink-white);
    font-weight: 700; font-size: 28px; letter-spacing: 1.5px;
    line-height: 1.15; text-transform: uppercase;
  }
  .locations {
    position: absolute; bottom: 52px; left: 0; right: 0;
    text-align: center;
    color: var(--ink-white); font-size: 14px; font-weight: 500; letter-spacing: 0.5px;
  }
  .locations .sep { color: var(--brand-yellow); margin: 0 6px; }
  /* Back */
  .card-back {
    background: var(--card-black);
    display: flex; align-items: center; justify-content: center; gap: 22px;
  }
  .person { text-align: right; }
  .person-name {
    color: var(--brand-red); font-weight: 500; font-size: 31px; letter-spacing: 0.3px;
  }
  .person-role {
    color: var(--ink-white); font-size: 15px; font-weight: 400; margin-top: 2px;
  }
  .divider { width: 1px; height: 96px; background: var(--divider); }
  .contacts { list-style: none; display: flex; flex-direction: column; gap: 5px; }
  .contact {
    display: flex; align-items: center; gap: 9px;
    color: var(--ink-white); font-size: 13.5px; font-weight: 400;
  }
  .contact svg { width: 15px; height: 15px; flex: none; }
</style>
</head>
<body>
<main class="canvas">
  <section class="card card-front" aria-label="Card front">
    <div class="brand">
      <span class="brand-dot"></span>
      <div class="brand-name">Harbourline Supply<br>Pty Ltd</div>
    </div>
    <p class="locations">Adelaide<span class="sep">•</span>Brisbane<span class="sep">•</span>Darwin</p>
  </section>

  <section class="card card-back" aria-label="Card back">
    <div class="person">
      <h1 class="person-name">Desmond Varrick</h1>
      <p class="person-role">General Manager</p>
    </div>
    <span class="divider"></span>
    <ul class="contacts">
      <li class="contact">
        <svg viewBox="0 0 16 16" aria-hidden="true"><rect x="4" y="1" width="8" height="14" rx="1.5" fill="none" stroke="#fbee3d" stroke-width="1.6"/><circle cx="8" cy="12.5" r="0.9" fill="#fbee3d"/></svg>
        0427 561 394
      </li>
      <li class="contact">
        <svg viewBox="0 0 16 16" aria-hidden="true"><rect x="1" y="3" width="14" height="10" fill="#fbee3d"/><path d="M1 3 L8 9 L15 3" fill="none" stroke="#070707" stroke-width="1.3"/></svg>
        dessie@harbourlinesupply.com.au
      </li>
      <li class="contact">
        <svg viewBox="0 0 16 16" aria-hidden="true"><rect x="1" y="3" width="14" height="10" fill="#fbee3d"/><path d="M1 3 L8 9 L15 3" fill="none" stroke="#070707" stroke-width="1.3"/></svg>
        dessie@outbackworks.com.au
      </li>
      <li class="contact">
        <svg viewBox="0 0 16 16" aria-hidden="true"><g fill="none" stroke="#fbee3d" stroke-width="1.3"><circle cx="8" cy="8" r="6.5"/><ellipse cx="8" cy="8" rx="3" ry="6.5"/><path d="M1.5 8 H14.5 M2.5 4.5 H13.5 M2.5 11.5 H13.5"/></g></svg>
        www.harbourlinesupply.com.au
      </li>
    </ul>
  </section>
</main>
</body>
</html>
```